Walk Beside The River

Business Card design

Target Market(s)

People who require support in the commnity

Industry/Entity Type

Mental Health Support

Contact Information for Business Card

Mental Health Support Rosalind Tavener walkbesidetheriver@mailcove.com.au 0481 637 092 PO Box 926 Wattlebrook QLD 4571

Colors
6B429C
8869AF
B7A5CE
E3DAEB
F3F0F8

Requirements
Must have
• Logo & details listed above
Should not have
• No red or orange

```html
<!DOCTYPE html>
<html lang="en">
<head>
<meta charset="utf-8">
<title>Walk Beside The River – Business Card</title>
<link rel="stylesheet" href="https://fonts.googleapis.com/css2?family=Montserrat:wght@500;800&display=swap">
<style>
  :root {
    --purple: #6B429C;
    --purple-mid: #8869AF;
    --lilac: #B7A5CE;
    --mist: #E3DAEB;
    --paper: #FFFFFF;
    --backdrop: #ECEAEF;
    --ink: #1E1B22;
  }
  * { box-sizing: border-box; margin: 0; padding: 0; }
  html, body {
    width: 1200px; height: 900px; overflow: hidden;
    background: var(--backdrop);
    font-family: "Montserrat", Arial, sans-serif;
  }
  .canvas {
    width: 1200px; height: 900px;
    display: flex; flex-direction: column; align-items: center; justify-content: center;
    gap: 40px;
  }
  .card {
    width: 600px; height: 343px;
    background: var(--paper);
    box-shadow: 0 6px 18px rgba(40, 30, 55, 0.18);
    display: flex; flex-direction: column; align-items: center; justify-content: center;
  }
  .brand {
    display: flex; align-items: center; gap: 18px;
  }
  .brand-dot {
    border-radius: 50%;
    background: var(--purple);
    flex: none;
  }
  .brand-name {
    color: var(--purple);
    font-weight: 800;
    text-transform: uppercase;
    letter-spacing: 0.06em;
    line-height: 1.15;
  }
  .card--front .brand-dot { width: 150px; height: 150px; }
  .card--front .brand-name { font-size: 26px; width: 230px; }
  .card--back .brand-dot { width: 80px; height: 80px; }
  .card--back .brand-name { font-size: 16px; width: 140px; }
  .card--back .brand { margin-bottom: 24px; }
  .role-line {
    color: var(--purple);
    font-weight: 800;
    font-size: 17px;
    letter-spacing: 0.01em;
    text-transform: uppercase;
    margin-bottom: 10px;
  }
  .contact-line {
    display: flex; align-items: center; gap: 8px;
    color: var(--ink);
    font-weight: 500;
    font-size: 15.5px;
    margin-top: 6px;
  }
  .contact-line + .contact-line { margin-top: 8px; }
  .icon { width: 16px; height: 16px; fill: var(--purple); flex: none; }
  .sep { width: 12px; }
</style>
</head>
<body>
<main class="canvas">
  <section class="card card--front">
    <div class="brand">
      <span class="brand-dot"></span>
      <span class="brand-name">Walk Beside The River</span>
    </div>
  </section>

  <section class="card card--back">
    <div class="brand">
      <span class="brand-dot"></span>
      <span class="brand-name">Walk Beside The River</span>
    </div>
    <p class="role-line">Mental Health Support Rosalind Tavener</p>
    <p class="contact-line">
      <svg class="icon" viewBox="0 0 16 16" aria-hidden="true"><path d="M8 0a5.5 5.5 0 0 0-5.5 5.5C2.5 9.6 8 16 8 16s5.5-6.4 5.5-10.5A5.5 5.5 0 0 0 8 0zm0 8a2.5 2.5 0 1 1 0-5 2.5 2.5 0 0 1 0 5z"/></svg>
      PO Box 926 Wattlebrook QLD 4571
    </p>
    <p class="contact-line">
      <svg class="icon" viewBox="0 0 16 16" aria-hidden="true"><path d="M3.6 1.2l2.2 2.6-1.3 1.8c.8 1.9 2.3 3.4 4.2 4.2l1.8-1.3 2.6 2.2-1.4 2.6C6.6 13.2 2.8 9.4 2.3 4.3z"/></svg>
      0481 637 092
      <span class="sep"></span>
      <svg class="icon" viewBox="0 0 16 16" aria-hidden="true"><path d="M1 3h14v10H1zM2.2 4.2v.4L8 8.8l5.8-4.2v-.4z"/></svg>
      walkbesidetheriver@mailcove.com.au
    </p>
  </section>
</main>
</body>
</html>
```